Modern looking signage for dental office.

Exterior signage for passing cars
Updates
Need extra days to review
Target Market(s)
Cars passing by
Font styles to use
Sans Serif
Colors
3276b5
Requirements
Must have
- Logo
- OPEN ON SUTURDAY AND SUNDAY
- NIGHT CLINIC AVAILABLE
- PLEASE USE THE FONT TYPE IN FILE 4 UPLOADED BELOW.
- (847) 302-7469
- Modern looking

```html
<!DOCTYPE html>
<html lang="en">
<head>
<meta charset="utf-8">
<title>Brightway Dental – Exterior Sign</title>
<link rel="stylesheet" href="https://fonts.googleapis.com/css2?family=Roboto:wght@300;700&family=Roboto+Condensed:wght@400&display=swap">
<style>
  :root {
    --page-bg: #e9ebee;
    --sign-white: #ffffff;
    --ink: #1a1a1a;
    --logo-ink: #3a3634;
    --brand-blue: #1656a0;
    --tab-grey: #5b5856;
    --bar-grey: #4a4746;
  }
  * { margin: 0; padding: 0; box-sizing: border-box; }
  html, body { width: 1200px; height: 1200px; overflow: hidden; }
  body {
    background: var(--page-bg);
    position: relative;
    font-family: "Roboto", Arial, sans-serif;
  }
  .sign {
    position: absolute;
    left: 50px; top: 290px;
    width: 1100px; height: 620px;
    background: var(--sign-white);
    overflow: hidden;
    box-shadow: 0 4px 18px rgba(0,0,0,0.12);
  }
  .brand {
    position: absolute;
    left: 170px; top: 70px;
    display: flex; align-items: center; gap: 30px;
  }
  .brand-circle {
    width: 190px; height: 190px;
    border: 3px solid var(--logo-ink);
    border-radius: 50%;
    flex: none;
  }
  .brand-text { display: flex; flex-direction: column; }
  .brand-name {
    font-family: "Roboto", Arial, sans-serif;
    font-weight: 300;
    font-size: 60px;
    line-height: 1;
    color: var(--logo-ink);
    letter-spacing: 1px;
    text-transform: uppercase;
    white-space: nowrap;
  }
  .brand-tagline {
    font-family: "Roboto Condensed", Arial, sans-serif;
    font-size: 30px;
    color: var(--logo-ink);
    margin-top: 14px;
    text-align: right;
    letter-spacing: 0.5px;
    white-space: nowrap;
  }
  .accent-bar {
    position: absolute;
    right: 30px; top: 10px;
    width: 10px; height: 290px;
    background: var(--bar-grey);
  }
  .night-band {
    position: absolute;
    left: 0; top: 360px;
    width: 690px; height: 120px;
    background: var(--brand-blue);
    border-top-right-radius: 14px;
    display: flex; align-items: center;
    padding-left: 70px;
    color: #fff;
    font-weight: 700;
    font-size: 62px;
    white-space: nowrap;
  }
  .weekend-tab {
    position: absolute;
    right: 0; top: 360px;
    width: 370px; height: 64px;
    background: var(--tab-grey);
    border-top-left-radius: 10px;
    border-bottom-left-radius: 10px;
    display: flex; align-items: center; justify-content: center;
    color: #fff;
    font-family: "Roboto Condensed", Arial, sans-serif;
    font-size: 24px;
    white-space: nowrap;
  }
  .phone {
    position: absolute;
    left: 400px; top: 478px;
    font-weight: 700;
    font-size: 88px;
    color: var(--ink);
    line-height: 1.1;
    white-space: nowrap;
  }
  .base-stripe {
    position: absolute;
    left: 0; bottom: 0;
    width: 100%; height: 22px;
    background: var(--brand-blue);
  }
</style>
</head>
<body>
  <div class="sign">
    <div class="brand">
      <div class="brand-circle"></div>
      <div class="brand-text">
        <div class="brand-name">Brightway Dental</div>
        <div class="brand-tagline">MODERN GENERAL DENTISTRY</div>
      </div>
    </div>
    <div class="accent-bar"></div>
    <div class="night-band">Night Clinic Available</div>
    <div class="weekend-tab">Open on Saturday and Sunday</div>
    <div class="phone">(847) 302-7469</div>
    <div class="base-stripe"></div>
  </div>
</body>
</html>
```